Fernhale Business Card Design

We are looking for a fresh business card design for our new logo. We would like a business card that is unique but friendly. We are in the window coverings business offering blinds, shutters and shades for homes.

Target Market(s)

Targeting the end-consumer

Industry/Entity Type

Business

Requirements
Must have
• Must have a dedicates space for a photo of our sales person. Must contain our new logo (attached).

```html
<!DOCTYPE html>
<html lang="en">
<head>
<meta charset="utf-8">
<title>Fernhale Business Card</title>
<link rel="stylesheet" href="https://fonts.googleapis.com/css2?family=Roboto+Condensed:wght@300;400;700&display=swap">
<style>
  :root {
    --stage: #ecebe8;
    --card-grey: #7e7e84;
    --card-grey-dark: #6f6f75;
    --card-white: #fbfbfb;
    --leaf-green: #8cc63f;
    --ink-white: #ffffff;
    --ink-grey: #8a8a8a;
    --photo-grey: #a9a9a9;
  }
  * { box-sizing: border-box; margin: 0; padding: 0; }
  html, body { width: 1200px; height: 886px; overflow: hidden; }
  body {
    background: var(--stage);
    font-family: "Roboto Condensed", Arial, sans-serif;
    position: relative;
  }
  .card {
    position: absolute;
    box-shadow: 0 6px 18px rgba(0,0,0,0.18);
  }
  /* Front */
  .card-front {
    left: 70px; top: 283px;
    width: 580px; height: 332px;
    background: linear-gradient(160deg, var(--card-grey) 0%, var(--card-grey-dark) 100%);
    color: var(--ink-white);
    overflow: hidden;
  }
  .accent-bar {
    position: absolute; right: 0; top: 0;
    width: 12px; height: 44px;
    background: var(--leaf-green);
  }
  .brand-feature {
    position: absolute; left: 36px; bottom: 36px;
    display: flex; flex-direction: column; align-items: flex-start; gap: 14px;
  }
  .brand-feature .brand-square {
    width: 150px; height: 150px; background: var(--leaf-green);
  }
  .brand-feature .brand-name {
    font-size: 40px; font-weight: 400; color: var(--ink-white); line-height: 1;
  }
  .contact-block {
    position: absolute; right: 40px; top: 26px;
    text-align: right;
  }
  .person-name {
    font-size: 21px; font-weight: 400; letter-spacing: 0.5px;
    color: var(--leaf-green); line-height: 1.1;
  }
  .person-role {
    font-size: 16px; font-weight: 400; line-height: 1.2;
    margin-bottom: 14px;
  }
  .address, .phones, .web {
    font-size: 15px; font-weight: 300; line-height: 1.3;
  }
  .address { margin-bottom: 10px; }
  .phones { margin-bottom: 10px; }
  .phone-line { display: flex; justify-content: flex-end; align-items: center; gap: 8px; }
  .phone-line svg { width: 11px; height: 11px; fill: var(--leaf-green); }
  .wordmark-front {
    position: absolute; right: 40px; bottom: 30px;
  }
  .wordmark-front .brand-name {
    font-size: 46px; font-weight: 400; color: var(--ink-white); line-height: 1;
  }
  /* Back */
  .card-back {
    left: 760px; top: 150px;
    width: 340px; height: 586px;
    background: var(--card-white);
    overflow: hidden;
  }
  .back-brand {
    position: absolute; left: 34px; top: 60px;
    display: flex; align-items: center; gap: 12px;
  }
  .back-brand .brand-square {
    width: 30px; height: 30px; background: var(--ink-grey);
  }
  .back-brand .brand-name {
    font-size: 40px; font-weight: 400; color: var(--ink-grey); line-height: 1;
  }
  .back-url {
    position: absolute; left: 36px; top: 112px;
    font-size: 13px; letter-spacing: 6px; color: var(--ink-grey);
  }
  .photo-slot {
    position: absolute; left: 40px; right: 0; bottom: 0; height: 350px;
    background: linear-gradient(180deg, #b3b3b3 0%, var(--photo-grey) 100%);
  }
</style>
</head>
<body>
  <section class="card card-front">
    <div class="accent-bar"></div>
    <div class="brand-feature">
      <span class="brand-square"></span>
      <span class="brand-name">Fernhale</span>
    </div>
    <div class="contact-block">
      <p class="person-name">DANA KELLERBY</p>
      <p class="person-role">CEO/FOUNDER</p>
      <p class="address">412 Alder Row<br>Bellmont, Oregon 97310</p>
      <div class="phones">
        <p class="phone-line">541 208 7716
          <svg viewBox="0 0 24 24"><path d="M6.6 10.8a15 15 0 0 0 6.6 6.6l2.2-2.2c.3-.3.7-.4 1-.2 1.1.4 2.3.6 3.6.6.6 0 1 .4 1 1V20c0 .6-.4 1-1 1A17 17 0 0 1 3 4c0-.6.4-1 1-1h3.5c.6 0 1 .4 1 1 0 1.3.2 2.5.6 3.6.1.3 0 .7-.2 1z"/></svg>
        </p>
        <p class="phone-line">541 309 4482
          <svg viewBox="0 0 24 24"><rect x="6" y="2" width="12" height="20" rx="2"/></svg>
        </p>
        <p class="phone-line">541 772 0365
          <svg viewBox="0 0 24 24"><rect x="3" y="5" width="18" height="14" rx="1"/></svg>
        </p>
      </div>
      <div class="web">
        <p class="phone-line">hello@fernhale.com
          <svg viewBox="0 0 24 24"><rect x="2" y="5" width="20" height="14" rx="1"/></svg>
        </p>
        <p class="phone-line">www.fernhale.com
          <svg viewBox="0 0 24 24"><circle cx="12" cy="12" r="10"/></svg>
        </p>
      </div>
    </div>
    <div class="wordmark-front">
      <span class="brand-name">Fernhale</span>
    </div>
  </section>

  <section class="card card-back">
    <div class="back-brand">
      <span class="brand-square"></span>
      <span class="brand-name">Fernhale</span>
    </div>
    <p class="back-url">www.fernhale.com</p>
    <div class="photo-slot" role="img" aria-label="Portrait photo of the sales person"></div>
  </section>
</body>
</html>
```